Varnik Holdings — Business Card Design Brief
Overview
Design a double-sided business card for Varnik Holdings that highlights our two service arms: Varnik Communications (telecommunications) and Varnik Energy (business energy solutions). The card should feel smart and stand out when handed to clients.

Objectives
Showcase our areas of specialty clearly.
Reflect the overall Varnik / Varnik Holdings brand while acknowledging both arms.
Explore using both logos (Communications + Energy) or one unified logo, depending on the design.

Deliverables
One double-sided business card design (front + back).

Content & Copy
Front (preferred): Logo: Varnik / Varnik Holdings
Descriptor: Business Communications | Business Energy
Back:My contact details and company details
Core products: Business Mobile • Telephony • Internet • Business Energy Solutions

Brand & Visual Direction
We have a group logo currently tailored more toward telecoms, plus a separate Varnik Energy logo.
Please explore layouts that use both logos or just one, whichever works best.
Color: I wouldn't mind seeing an option using our the Blue/Purple gradient from our website (varnik-example.co.uk), but also open to non-gradient approaches and other colours..

Overall look: Smart, modern, and distinctive.
Format & Print Specs
Double-sided business card format. (Use a standard size

Must-Haves
Front: Varnik wording or Varnik Holdings wording with atleast 1 logo also on front “Business Communications | Business Energy.”

Back: Contact + company details and core products.
A design that stands out while remaining professional.

Nice-to-Have Options
A gradient version using our site’s Blue/Purple gradient.
A non-gradient version.
A dual-logo treatment versus a single-logo treatment.

Thanks
Owen

```html
<!DOCTYPE html>
<html lang="en">
<head>
<meta charset="utf-8">
<title>Varnik Holdings – Business Card</title>
<link href="https://fonts.googleapis.com/css2?family=Poppins:wght@700&family=Roboto:wght@400;700&display=swap" rel="stylesheet">
<style>
  :root {
    --page: #f0f0f0;
    --white: #ffffff;
    --navy: #231f5c;
    --ink: #1a1a1a;
    --green: #22a84a;
    --lime: #c9d42a;
    --blue: #2f6fc0;
    --purple: #2a2a7a;
  }
  * { box-sizing: border-box; margin: 0; padding: 0; }
  html, body { width: 1200px; height: 990px; overflow: hidden; background: var(--page); }
  body { position: relative; font-family: "Roboto", sans-serif; }

  .card {
    position: absolute;
    left: 245px;
    width: 712px;
    height: 407px;
    border-radius: 46px;
    background: linear-gradient(90deg, var(--green), var(--lime));
    overflow: hidden;
  }
  .card::before {
    content: "";
    position: absolute;
    left: 5px; top: 0; right: 0; bottom: 5px;
    border-radius: 44px;
    background: var(--white);
  }
  .card > * { position: absolute; }
  .card--front { top: 67px; }
  .card--back { top: 515px; }

  .brand-mark { fill: none; stroke-width: 9; }
  .brand-name {
    font-family: "Poppins", sans-serif;
    font-weight: 700;
    color: var(--navy);
    letter-spacing: 1px;
    line-height: 1;
  }

  /* front */
  .card--front .brand-mark-svg { left: 310px; top: 96px; }
  .card--front .brand-name { left: 0; right: 0; top: 236px; text-align: center; font-size: 62px; }
  .descriptor {
    left: 0; right: 0; top: 355px;
    text-align: center;
    font-size: 19px;
    color: var(--navy);
    letter-spacing: 0.3px;
  }

  /* back */
  .card--back .brand-mark-svg { left: 40px; top: 108px; }
  .card--back .brand-name { left: 44px; top: 240px; font-size: 58px; }
  .divider {
    left: 355px; top: 72px;
    width: 1px; height: 262px;
    background: linear-gradient(180deg, rgba(120,180,60,0), #8cbf3a 20%, #8cbf3a 80%, rgba(120,180,60,0));
  }
  .person { left: 415px; top: 92px; }
  .person-name {
    font-size: 40px;
    font-weight: 700;
    line-height: 1.05;
    background: linear-gradient(90deg, var(--green), var(--lime));
    -webkit-background-clip: text;
    background-clip: text;
    color: transparent;
  }
  .person-role { font-size: 19px; color: var(--ink); margin-top: 2px; }
  .address { left: 415px; top: 168px; font-size: 19px; line-height: 24px; color: var(--ink); font-style: normal; }
  .contacts { left: 440px; top: 232px; list-style: none; font-size: 19px; line-height: 24px; color: var(--ink); }

  .product-band {
    left: 5px; right: 0; top: 348px; height: 32px;
    background: linear-gradient(90deg, var(--green) 0%, #9cc83a 55%, var(--lime) 85%, var(--blue) 93%, var(--purple) 100%);
    display: flex; align-items: center;
  }
  .products {
    list-style: none; display: flex; gap: 10px;
    padding-left: 24px;
    font-size: 18px; color: var(--white);
  }
  .products li::before {
    content: ""; display: inline-block;
    width: 8px; height: 8px; border-radius: 50%;
    background: var(--white); margin-right: 6px; vertical-align: 3px;
  }
  .band-brand {
    position: absolute; right: 24px; top: 5px;
    font-family: "Poppins", sans-serif; font-weight: 700;
    font-size: 15px; color: var(--white); letter-spacing: 0.5px;
  }
</style>
</head>
<body>
  <section class="card card--front" aria-label="Business card front">
    <svg class="brand-mark-svg" width="92" height="92" viewBox="0 0 92 92" aria-hidden="true">
      <circle class="brand-mark" cx="46" cy="46" r="40" stroke="#3461b0"/>
    </svg>
    <div class="brand-name">VARNIK</div>
    <p class="descriptor">Business Communications | Business Energy</p>
  </section>

  <section class="card card--back" aria-label="Business card back">
    <svg class="brand-mark-svg" width="128" height="128" viewBox="0 0 128 128" aria-hidden="true">
      <circle class="brand-mark" cx="64" cy="64" r="58" stroke="#2fae4a"/>
    </svg>
    <div class="brand-name">VARNIK</div>
    <div class="divider"></div>

    <div class="person">
      <h1 class="person-name">Marta Kovena</h1>
      <p class="person-role">Founder &amp; CEO</p>
    </div>
    <address class="address">24 Example Lane, Manchester,<br>England, M1 0AA</address>
    <ul class="contacts">
      <li>+44 0161 555 0142</li>
      <li>www.varnik-example.co.uk</li>
      <li>info@varnik-example.co.uk</li>
    </ul>

    <div class="product-band">
      <ul class="products">
        <li>Business Mobile</li>
        <li>Telephony</li>
        <li>Internet</li>
        <li>Business Energy Solutions</li>
      </ul>
      <span class="band-brand">VARNIK</span>
    </div>
  </section>
</body>
</html>
```